Buch-/E-Book-Cover für Erstveröffentlichung eines kleinen Fantasyromans
Zielgruppe
Ich habe gerade mein erstes kleineres Buch fertig geschrieben und möchte es nun über Self Publishing selbst herausbringen.
Das Buch ist eine eher niedliche kleine Geschichte über ein eher gruselig aussehendes Lebenwesen, das sich mit einem kleinen Mädchen anfreundet. Gelesen werden kann das Buch ab 12. Nach oben hin sind denke ich mal keine Grenzen.
Aufgabenstellung
Titel: Die Nebelkrähe - Ein seltsamer Sommerbund
Ich brauche ein Cover für die E-Book und Softcover Ausgabe.
Es handelt sich um ein Buch in den Maßen 12,85x19,83. Genaueres kann hier dem Anhang entnommen werden. Verlio erstellt einem extra eine Vorlage mit allen genauen Maßen und Rändern, die eingehalten werden müssen.
Das Werk befindet sich im Moment im Lektrorat. Es kann also kleine Abweichungen zum Buchrücken geben, falls sich die Seitenzahl noch ändern sollte.
UPDATE: Das Lektorat ist nun abgeschlossen und die endgültigen Maße sind nun in der Datei enthalten.
Auf der Rückseite soll noch der Klappentext stehen. Dieser ist auch im Anhang beigefügt.
UPDATE: Die Datei wurde nochmal aktualisiert, weil noch weitere Seiten mit dabei waren, die nicht mit rein gehören.
Wer ein wenig Inspiration benötigt, kann sich auch meine Pinnwand zum Projekt auf Klebwand ansehen.
https://www.klebwand-beispiel.de/ErzaehlNest/projekt-die-nebelkraehe/
Für Leute, die noch genaueren Einblick in die Atmosphäre haben wollen, gibt es die ersten Kapitel auch in der unkorrigierten Version auf meinem Blog zum lesen.
http://erzaehl-nest.blogfeld-beispiel.com/tagged/die-nebelkraehe/chrono

```html
<!DOCTYPE html>
<html lang="de">
<head>
<meta charset="utf-8">
<title>Die Nebelkrähe – Buchumschlag</title>
<link rel="stylesheet" href="https://fonts.googleapis.com/css2?family=Antonio:wght@700&family=Pathway+Gothic+One&display=swap">
<style>
  :root {
    --night: #000000;
    --blood-dark: #1c0000;
    --blood-mid: #6a0000;
    --blood-bright: #e10000;
    --shade: #140000;
    --panel: rgba(78, 78, 78, 0.62);
    --panel-solid: #444444;
    --ink-light: #ffffff;
  }
  html, body {
    margin: 0;
    padding: 0;
    width: 1200px;
    height: 909px;
    overflow: hidden;
    background: var(--night);
  }
  .cover {
    position: relative;
    width: 1200px;
    height: 909px;
    overflow: hidden;
  }
  .scene-art {
    position: absolute;
    inset: 0;
    background:
      radial-gradient(ellipse 420px 260px at 120px 620px, rgba(255, 40, 40, 0.55), transparent 70%),
      radial-gradient(ellipse 420px 280px at 1080px 600px, rgba(255, 20, 20, 0.55), transparent 70%),
      linear-gradient(to bottom, var(--blood-dark) 0%, var(--blood-mid) 35%, var(--blood-bright) 70%, var(--blood-bright) 75.5%, var(--night) 76%, var(--night) 100%);
  }
  .shadow-figure {
    position: absolute;
    left: 620px;
    top: 0;
    width: 580px;
    height: 690px;
    background:
      radial-gradient(ellipse 110px 200px at 300px 150px, rgba(20, 0, 0, 0.9), rgba(20, 0, 0, 0.55) 60%, transparent 100%),
      radial-gradient(ellipse 290px 260px at 300px 640px, rgba(20, 0, 0, 0.75), rgba(20, 0, 0, 0.35) 60%, transparent 100%);
  }
  .silhouette-group {
    position: absolute;
    left: 880px;
    top: 420px;
    width: 320px;
    height: 270px;
    background: radial-gradient(ellipse 150px 120px at 170px 170px, rgba(0, 0, 0, 0.75), transparent 80%);
  }
  .back-panel {
    position: absolute;
    left: 73px;
    top: 0;
    width: 445px;
    height: 909px;
    background: linear-gradient(to bottom, var(--panel) 0%, var(--panel) 75.8%, var(--panel-solid) 76%, var(--panel-solid) 100%);
  }
  .blurb {
    position: absolute;
    left: 73px;
    top: 54px;
    width: 445px;
    margin: 0;
    font-family: "Pathway Gothic One", "Arial Narrow", sans-serif;
    font-size: 18.6px;
    line-height: 37.3px;
    color: var(--ink-light);
    text-align: center;
    white-space: nowrap;
  }
  .blurb span { display: block; }
  .author {
    position: absolute;
    left: 804px;
    top: 60px;
    width: 200px;
    text-align: center;
    font-family: "Antonio", "Arial Narrow", sans-serif;
    font-weight: 700;
    font-size: 46px;
    line-height: 1;
    color: var(--ink-light);
    letter-spacing: -1px;
  }
  .title {
    margin: 0;
    font-weight: 700;
  }
  .title-article,
  .title-main,
  .subtitle {
    position: absolute;
    left: 732px;
    width: 400px;
    margin: 0;
    text-align: center;
    font-family: "Antonio", "Arial Narrow", sans-serif;
    font-weight: 700;
    color: var(--ink-light);
    line-height: 1;
    white-space: nowrap;
  }
  .title-article {
    top: 620px;
    font-size: 66px;
    letter-spacing: -2px;
  }
  .title-main {
    top: 692px;
    font-size: 78px;
    letter-spacing: -2px;
  }
  .subtitle {
    top: 800px;
    font-size: 36px;
    letter-spacing: -1px;
  }
</style>
</head>
<body>
<div class="cover">
  <div class="scene-art" role="img" aria-label="Rote Abendszene mit schwarzen Silhouetten von Bäumen mit Schaukeln, spielenden Mädchen und einem Gartentor"></div>
  <div class="shadow-figure" role="img" aria-label="Große dunkle Schattengestalt mit roten Augen im Hintergrund"></div>
  <div class="silhouette-group" role="img" aria-label="Silhouetten zweier Mädchen an einer Schaukel neben einem Flügel"></div>

  <div class="back-panel"></div>
  <p class="blurb">
    <span>Ich wusste nicht wer ich war.</span>
    <span>Ich wusste nicht was ich war.</span>
    <span>Meine neue Gestalt war schwarz</span>
    <span>von oben bis unten.</span>
    <span>Schwarz wie ein Schatten</span>
    <span>mit stechenden roten Augen.</span>
    <span>Ich wusste nicht wie ich</span>
    <span>in diese Grotte gekommen war.</span>
    <span>Ich wusste nicht</span>
    <span>warum ich durch dieses seltsame schwarze Loch,</span>
    <span>durch das man nichts sehen konnte,</span>
    <span>nach draußen gelangen konnte.</span>
    <span>Mein neues Zuhause befand sich in einem Wald.</span>
    <span>Viele Menschen gab es in hier nicht.</span>
    <span>Was ich aber wusste, war dass ich anders war als all die normalen Menschen.</span>
    <span>Anders machte den Menschen Angst.</span>
    <span>Doch in diesem Punkt sollte ich eines besseren belehrt werden,</span>
    <span>als ich ein kleines Mädchen traf, welches mich sofort in ihr Herz schloss</span>
  </p>

  <div class="author">AUTOR</div>
  <h1 class="title">
    <span class="title-article">Die</span>
    <span class="title-main">Nebelkrähe</span>
  </h1>
  <p class="subtitle">ein seltsamer Sommerbund</p>
</div>
</body>
</html>
```